Brightfen Business Card Redesign & Logo Update

We need to update our business cards to something more modern and fresh. Brightfen can provide the current color schemes and old design examples, but welcome creativity in helping us with this redesign. PLEASE NOTE that we no longer utilize the "tree" and/or "leaf" imagery in our branding. If able would apprecaite an update on the quality of our "words only" logo in Ai. / PNG formats too.

Target Market(s)

Investors, landowners, corporate partners, contractors

Industry/Entity Type

Environmental Restoration & Conservation

Contact Information for Business Card

Logo, persons name, title, mailing address, phone and email, website url

Font styles to use
Other font styles liked:
• Merriweather

Requirements
Nice to have
• Logo, persons name, title, mailing address, phone and email, website url, but open to ideams
Should not have
• No all back backgrounds

```html
<!DOCTYPE html>
<html lang="en">
<head>
<meta charset="utf-8">
<title>Brightfen Business Card</title>
<link href="https://fonts.googleapis.com/css2?family=Oswald:wght@600&family=Open+Sans:wght@400;600&display=swap" rel="stylesheet">
<style>
  :root {
    --backdrop: #3b3b3b;
    --card: #161616;
    --card-edge: #1f7a3a;
    --green: #18803f;
    --orange: #ec7a1c;
    --white: #f2f2f2;
    --grey: #cfcfcf;
    --emboss: #2a2a2a;
  }
  * { margin: 0; padding: 0; box-sizing: border-box; }
  html, body {
    width: 1200px; height: 801px; overflow: hidden;
    background: var(--backdrop);
  }
  .stage {
    width: 1200px; height: 801px;
    display: flex; align-items: center; justify-content: center; gap: 50px;
  }
  .card {
    position: relative;
    width: 525px; height: 300px;
    background: var(--card);
    border: 2px solid var(--card-edge);
    border-radius: 18px;
    overflow: hidden;
    box-shadow: 0 18px 40px rgba(0,0,0,.45);
  }
  .brand-name {
    font-family: "Oswald", sans-serif;
    font-weight: 600;
    text-transform: uppercase;
    line-height: 1;
  }
  .front .brand-name {
    position: absolute; left: 40px; top: 34px;
    font-size: 62px; color: var(--orange); letter-spacing: 1px;
  }
  .tagline {
    font-family: "Oswald", sans-serif;
    font-weight: 600;
    text-transform: uppercase;
    line-height: 1;
  }
  .front .tagline {
    position: absolute; left: 42px; top: 104px;
    font-size: 16px; color: var(--white); letter-spacing: .3px;
  }
  .person {
    position: absolute; left: 42px; top: 162px;
    font-family: "Open Sans", sans-serif;
  }
  .person-name {
    font-weight: 600; font-size: 19px; color: var(--orange);
    text-transform: uppercase; letter-spacing: .5px;
  }
  .person-title {
    font-size: 15px; color: var(--white); text-align: right; margin-top: 2px;
  }
  .divider {
    position: absolute; left: 250px; top: 152px;
    width: 2px; height: 66px; background: var(--orange);
  }
  .contact-list {
    position: absolute; left: 268px; top: 150px;
    list-style: none;
    font-family: "Open Sans", sans-serif; font-size: 14px; color: var(--grey);
  }
  .contact-list li {
    display: flex; align-items: center; gap: 8px; height: 23px;
  }
  .contact-list svg { width: 12px; height: 12px; flex: none; }
  .address-band {
    position: absolute; left: 0; right: 0; bottom: 16px; height: 34px;
    background: var(--green);
    display: flex; align-items: center; padding-left: 42px;
    font-family: "Open Sans", sans-serif; font-size: 15px; color: var(--white);
  }
  .back {
    display: flex; flex-direction: column; align-items: center; justify-content: center;
  }
  .back .brand-name {
    font-size: 84px; color: var(--emboss); letter-spacing: 1px;
  }
  .back .tagline {
    font-size: 22px; color: var(--emboss); margin-top: 4px;
  }
</style>
</head>
<body>
<main class="stage">
  <section class="card front">
    <div class="brand-name">Brightfen</div>
    <div class="tagline">Environmental Credit Company</div>

    <div class="person">
      <div class="person-name">Dara Kellner</div>
      <div class="person-title">President</div>
    </div>

    <div class="divider"></div>

    <ul class="contact-list">
      <li>
        <svg viewBox="0 0 12 12" aria-hidden="true"><path fill="#18803f" d="M2.5 1 4.3 3 3.3 4.3c.7 1.6 1.8 2.7 3.4 3.4L8 6.7 11 8.5 10 11C5.2 11 1 6.8 1 2Z"/></svg>
        555-014-2290
      </li>
      <li>
        <svg viewBox="0 0 12 12" aria-hidden="true"><rect x="1" y="2.5" width="10" height="7" rx="1" fill="#18803f"/><path d="M1.5 3 6 6.5 10.5 3" stroke="#161616" fill="none"/></svg>
        dkellner@brightfen.com
      </li>
      <li>
        <svg viewBox="0 0 12 12" aria-hidden="true"><circle cx="6" cy="6" r="5" fill="#18803f"/><path d="M1 6h10M6 1c-2.2 2.8-2.2 7.2 0 10M6 1c2.2 2.8 2.2 7.2 0 10" stroke="#161616" stroke-width=".8" fill="none"/></svg>
        www.brightfen.com
      </li>
    </ul>

    <div class="address-band">1840 Harbor Crest Way, Marlow Bay CA 90210</div>
  </section>

  <section class="card back">
    <div class="brand-name">Brightfen</div>
    <div class="tagline">Environmental Credit Company</div>
  </section>
</main>
</body>
</html>
```